Business card design for holistic health care clinic

We need a double-sided business card design for our holistic health care clinic that integrates our logo design and also its color scheme. My business is called Valmira. It is an integrative medicine clinic. You have already done the logo for me. Please ensure an elegant and upscale design that is not cluttered, but still has all the necessary information (please see below for details).

Target Market(s)

Wellness, fitness, rehabilitation for educated, well-traveled open-minded clients who are focused on natural, organic, balanced and preventive healthcare and lifestyle.

Industry/Entity Type

Medical

Contact Information for Business Card

Modern, clean.

Number of Pages Required

1 page

Font styles to use
Serif
Sans Serif

Colors

Designer to choose colors to be used in the design.

Requirements
Must have
• Logo on one side, all other information on the other side.
• Other information should include:
• Tobias Wrenfeld - DOE, CPT, LMT
• 4100 East Marrow Drive
• Austin, TX 78119
• 512 555 0148
• 818 555 0192
• info@ValmiraHealth.example
• t.wrenfeld@ValmiraHealth.example
Nice to have
• Darker background on front - but not totally black - shaded/dark gray.

```html
<!DOCTYPE html>
<html lang="en">
<head>
<meta charset="utf-8">
<title>Valmira – Business Cards</title>
<link href="https://fonts.googleapis.com/css2?family=Nunito:wght@400;700;800&display=swap" rel="stylesheet">
<style>
  :root {
    --backdrop: #2b2b2b;
    --brand-blue: #0b8fd0;
    --card-gray: #a6a6a6;
    --card-white: #f2f2f2;
    --text-light: #ffffff;
    --text-dark: #444444;
  }
  * { margin: 0; padding: 0; box-sizing: border-box; }
  html, body { width: 1200px; height: 961px; overflow: hidden; }
  body {
    background: var(--backdrop);
    font-family: "Nunito", sans-serif;
    position: relative;
  }
  .card {
    position: absolute;
    width: 453px;
    height: 258px;
    overflow: hidden;
    box-shadow: 0 3px 8px rgba(0,0,0,.45);
  }
  .card--gray { background: var(--card-gray); }
  .card--white { background: var(--card-white); }

  .front-gray { left: 133px; top: 206px; }
  .front-white { left: 617px; top: 206px; }
  .back-white { left: 132px; top: 496px; }
  .back-gray { left: 615px; top: 496px; }

  .brand { position: absolute; color: var(--brand-blue); }
  .brand__name {
    font-weight: 800;
    letter-spacing: 0.5px;
    line-height: 1;
    text-transform: uppercase;
  }
  .brand__subtitle { font-weight: 700; line-height: 1; }

  .front .brand { left: 27px; top: 49px; }
  .front .brand__name { font-size: 37px; }
  .front .brand__subtitle { font-size: 11.5px; margin-top: 4px; margin-left: 3px; }

  .back .brand { left: 0; right: 0; top: 118px; text-align: center; }
  .back .brand__name { font-size: 54px; }
  .back .brand__subtitle { font-size: 16px; margin-top: 4px; }

  .contact {
    position: absolute;
    left: 28px;
    top: 122px;
    font-size: 11.5px;
    line-height: 13px;
  }
  .card--gray .contact { color: var(--text-light); }
  .card--white .contact { color: var(--text-dark); }
  .contact__address { margin-bottom: 9px; }
  .contact__line { display: flex; align-items: center; height: 14.5px; }
  .contact__line svg { width: 10px; height: 10px; margin-right: 6px; fill: var(--brand-blue); flex: none; }

  .person {
    position: absolute;
    right: 34px;
    top: 150px;
    text-align: right;
    color: var(--brand-blue);
  }
  .person__name { font-size: 16px; font-weight: 800; text-transform: uppercase; line-height: 1; }
  .person__credentials { font-size: 9.5px; font-weight: 800; letter-spacing: .5px; margin-top: 3px; }

  .tagline-band {
    position: absolute;
    left: 0; right: 0; bottom: 0;
    height: 26px;
    background: var(--brand-blue);
    color: var(--text-light);
    font-size: 10.5px;
    font-weight: 700;
    display: flex;
    align-items: center;
    justify-content: center;
  }
</style>
</head>
<body>

<section class="card card--gray front front-gray">
  <div class="brand">
    <div class="brand__name">Valmira</div>
    <div class="brand__subtitle">Integrative Holistic Medicine</div>
  </div>
  <div class="contact">
    <div class="contact__address">4100 East Marrow Drive<br>Austin, TX 78119</div>
    <div class="contact__line"><svg viewBox="0 0 10 10"><path d="M2 0.5l2 2-1 1.2c.6 1.3 1.5 2.2 2.8 2.8L7 5.5l2 2L8 9.3C4.2 9 1 5.8.7 2z"/></svg>512 555 0148</div>
    <div class="contact__line"><svg viewBox="0 0 10 10"><path d="M2.5 0h5v10h-5zM3.5 1v7h3V1z"/></svg>818 555 0192</div>
    <div class="contact__line"><svg viewBox="0 0 10 10"><path d="M0 2h10v6H0zM0 2l5 3.5L10 2" stroke="#fff" stroke-width=".6"/></svg>t.wrenfeld@ValmiraHealth.example</div>
    <div class="contact__line"><svg viewBox="0 0 10 10"><circle cx="5" cy="5" r="5"/><path d="M5 0v10M0 5h10" stroke="#fff" stroke-width=".6"/></svg>www.ValmiraHealth.example</div>
  </div>
  <div class="person">
    <div class="person__name">Tobias Wrenfeld</div>
    <div class="person__credentials">DOE, CPT, LMT</div>
  </div>
  <div class="tagline-band">At Valmira, it’s all about you – your health, your objectives</div>
</section>

<section class="card card--white front front-white">
  <div class="brand">
    <div class="brand__name">Valmira</div>
    <div class="brand__subtitle">Integrative Holistic Medicine</div>
  </div>
  <div class="contact">
    <div class="contact__address">4100 East Marrow Drive<br>Austin, TX 78119</div>
    <div class="contact__line"><svg viewBox="0 0 10 10"><path d="M2 0.5l2 2-1 1.2c.6 1.3 1.5 2.2 2.8 2.8L7 5.5l2 2L8 9.3C4.2 9 1 5.8.7 2z"/></svg>512 555 0148</div>
    <div class="contact__line"><svg viewBox="0 0 10 10"><path d="M2.5 0h5v10h-5zM3.5 1v7h3V1z"/></svg>818 555 0192</div>
    <div class="contact__line"><svg viewBox="0 0 10 10"><path d="M0 2h10v6H0zM0 2l5 3.5L10 2" stroke="#f2f2f2" stroke-width=".6"/></svg>t.wrenfeld@ValmiraHealth.example</div>
    <div class="contact__line"><svg viewBox="0 0 10 10"><circle cx="5" cy="5" r="5"/><path d="M5 0v10M0 5h10" stroke="#f2f2f2" stroke-width=".6"/></svg>www.ValmiraHealth.example</div>
  </div>
  <div class="person">
    <div class="person__name">Tobias Wrenfeld</div>
    <div class="person__credentials">DOE, CPT, LMT</div>
  </div>
  <div class="tagline-band">At Valmira, it’s all about you – your health, your objectives</div>
</section>

<section class="card card--white back back-white">
  <div class="brand">
    <div class="brand__name">Valmira</div>
    <div class="brand__subtitle">Integrative Holistic Medicine</div>
  </div>
</section>

<section class="card card--gray back back-gray">
  <div class="brand">
    <div class="brand__name">Valmira</div>
    <div class="brand__subtitle">Integrative Holistic Medicine</div>
  </div>
</section>

</body>
</html>
```